BRIVAN 2026 Flyer for Conference

BRIVAN needs a design for a 1-page flyer that we will hand out at an upcoming event & then later post online as a pdf. There are 3 elements which need to be on the flyer:

1) A logo. This should be prominent on the design (e.g., in the middle). The flyer should use the colors that are in that logo (e.g., for accents, design elements, and/or text; not all of these have to be used):
Dark blue: #185577
Med blue: #327C9A
Teal: #4EB1C2
Light Teal: #9EDBE6

2) The conference theme -- Oceans of Knowledge: Diving into Information Literacy -- should be at the flyer's top.

3) Finally, these six tracks should be listed below the theme and the logo (it's font size should be at least a couple sizes smaller than the size used for the theme):
- Pearls of Pedagogy: Teaching Techniques that Work
- The Depth Gauge: Measuring Instructional Impact
- Techtonic Shifts: Innovation and Educational Technology
- Captain's Log: Navigating Leadership in Library Instruction
- Swimming Together: Collaborating with Others
- The Bermuda Triangle: Exploring (Seemingly) Eternal Challenges

Font styles to use
Sans Serif

Colors
0094D4
00A9DD
6FCCEA
C7EBF8
E9F6FB

Requirements
Must have
• The 3 elements listed in the description: 1) the logo, 2) the text of the theme and 3) the text for the tracks.

```html
<!DOCTYPE html>
<html lang="en">
<head>
<meta charset="utf-8">
<title>BRIVAN 2026 – Oceans of Knowledge</title>
<link rel="stylesheet" href="https://fonts.googleapis.com/css2?family=Montserrat:wght@500;600;700&family=Roboto+Condensed:wght@400;500&display=swap">
<style>
  :root {
    --dark-blue: #185577;
    --med-blue: #327C9A;
    --teal: #4EB1C2;
    --light-teal: #9EDBE6;
    --band: #EEF7FA;
    --card: #F1F8FA;
    --card-edge: #D6E9EF;
    --ink: #222222;
    --white: #FFFFFF;
  }
  * { margin: 0; padding: 0; box-sizing: border-box; }
  html, body { width: 952px; height: 1200px; overflow: hidden; background: var(--white); }
  .flyer { position: relative; width: 952px; height: 1200px; background: var(--white); font-family: "Montserrat", sans-serif; color: var(--ink); }

  .brand { position: absolute; left: 52px; top: 96px; display: flex; align-items: center; gap: 12px; }
  .brand-dot { width: 34px; height: 34px; border-radius: 50%; background: var(--teal); }
  .brand-name { font-family: "Montserrat", sans-serif; font-weight: 700; font-size: 36px; color: var(--dark-blue); letter-spacing: 0.5px; }

  .event-tag { position: absolute; left: 495px; top: 40px; width: 412px; height: 166px; }
  .event-tag-shape { position: absolute; inset: 0; }
  .event-tag-text { position: absolute; left: 0; right: 0; top: 44px; text-align: center; font-family: "Roboto Condensed", sans-serif; color: var(--dark-blue); line-height: 1.15; padding-left: 10px; }
  .event-city { font-size: 42px; }
  .event-date { font-size: 34px; }

  .theme { position: absolute; left: 0; top: 272px; width: 952px; height: 190px; background: var(--band); border-top: 1px solid var(--card-edge); border-bottom: 1px solid var(--card-edge); display: flex; flex-direction: column; justify-content: center; align-items: center; text-align: center; }
  .theme-title { font-family: "Roboto Condensed", sans-serif; font-weight: 400; font-size: 62px; color: var(--dark-blue); line-height: 1.25; }

  .tracks-title { position: absolute; left: 0; width: 952px; top: 515px; text-align: center; font-family: "Roboto Condensed", sans-serif; font-weight: 400; font-size: 62px; color: var(--ink); }

  .tracks { position: absolute; left: 48px; top: 618px; width: 857px; display: grid; grid-template-columns: 420px 420px; column-gap: 17px; row-gap: 14px; list-style: none; }
  .track { height: 122px; background: var(--card); border: 1.5px solid var(--card-edge); display: flex; align-items: center; padding-left: 20px; }
  .track-icon { flex: none; width: 62px; height: 62px; border-radius: 8px; background: var(--light-teal); margin-right: 33px; }
  .track-name { font-weight: 600; font-size: 21px; color: var(--dark-blue); margin-bottom: 6px; }
  .track-desc { font-weight: 500; font-size: 16px; line-height: 1.3; color: var(--ink); }

  .footer { position: absolute; left: 0; top: 1060px; width: 952px; height: 140px; }
  .footer-wave { position: absolute; inset: 0; }
  .contact { position: absolute; left: 0; right: 0; top: 46px; text-align: center; color: var(--white); }
  .contact-label { font-weight: 600; font-size: 17px; line-height: 20px; }
  .contact-phone { display: inline-flex; align-items: center; gap: 14px; margin-top: 4px; font-family: "Roboto Condensed", sans-serif; font-size: 42px; line-height: 50px; }
  .phone-icon { flex: none; }
</style>
</head>
<body>
<main class="flyer">
  <header>
    <div class="brand">
      <span class="brand-dot"></span>
      <span class="brand-name">BRIVAN 2026</span>
    </div>

    <div class="event-tag">
      <svg class="event-tag-shape" viewBox="0 0 412 166" width="412" height="166" aria-hidden="true">
        <polygon points="37,3 406,28 392,126 24,162" fill="none" stroke="var(--dark-blue)" stroke-width="6"/>
        <polygon points="0,30 399,4 364,150 16,148" fill="var(--light-teal)"/>
        <polyline points="392,70 392,126 350,131" fill="none" stroke="var(--dark-blue)" stroke-width="6"/>
      </svg>
      <div class="event-tag-text">
        <div class="event-city">NORFOLK, VA</div>
        <div class="event-date">MAY 07-09, 2026</div>
      </div>
    </div>
  </header>

  <section class="theme">
    <h1 class="theme-title">Oceans of Knowledge:<br>Diving Into Information Literacy</h1>
  </section>

  <h2 class="tracks-title">The Six Tracks</h2>

  <ul class="tracks">
    <li class="track">
      <div class="track-icon" role="img" aria-label="Icon of a lightbulb with a gear and arrows"></div>
      <div><div class="track-name">Pearls of Pedagogy</div><div class="track-desc">Teaching Techniques that Work</div></div>
    </li>
    <li class="track">
      <div class="track-icon" role="img" aria-label="Icon of a presenter beside a rising chart"></div>
      <div><div class="track-name">The Depth Gauge</div><div class="track-desc">Measuring Instructional Impact</div></div>
    </li>
    <li class="track">
      <div class="track-icon" role="img" aria-label="Icon of a lightbulb with connected circuit nodes"></div>
      <div><div class="track-name">Techtonic Shifts</div><div class="track-desc">Innovation and Educational<br>Technology</div></div>
    </li>
    <li class="track">
      <div class="track-icon" role="img" aria-label="Icon of a gear with arrows pointing outward"></div>
      <div><div class="track-name">Captain's Log</div><div class="track-desc">Navigating Leadership in Library<br>Instruction</div></div>
    </li>
    <li class="track">
      <div class="track-icon" role="img" aria-label="Icon of a handshake surrounded by people"></div>
      <div><div class="track-name">Swimming Together</div><div class="track-desc">Collaborating with Others</div></div>
    </li>
    <li class="track">
      <div class="track-icon" role="img" aria-label="Icon of a figure pushing a gear up a slope"></div>
      <div><div class="track-name">The Bermuda Triangle</div><div class="track-desc">Exploring (Seemingly) Eternal<br>Challenges</div></div>
    </li>
  </ul>

  <footer class="footer">
    <svg class="footer-wave" viewBox="0 0 952 140" width="952" height="140" preserveAspectRatio="none" aria-hidden="true">
      <path d="M0,85 Q476,-65 952,85 L952,140 L0,140 Z" fill="var(--teal)"/>
      <path d="M0,92 Q476,-55 952,92 L952,140 L0,140 Z" fill="var(--white)"/>
      <path d="M0,95 Q476,-47 952,95 L952,140 L0,140 Z" fill="var(--dark-blue)"/>
    </svg>
    <div class="contact">
      <div class="contact-label">For More Information Contact Us</div>
      <div class="contact-phone">
        <svg class="phone-icon" width="40" height="40" viewBox="0 0 40 40" aria-hidden="true">
          <circle cx="20" cy="20" r="18" fill="none" stroke="var(--white)" stroke-width="2.5"/>
          <path d="M14 10 l5 5 -3 3 q2 5 6 7 l3 -3 5 5 -3 3 q-10 0 -16 -13 z" fill="none" stroke="var(--white)" stroke-width="2.2" stroke-linejoin="round"/>
        </svg>
        <span>0131 555 0148</span>
      </div>
    </div>
  </footer>
</main>
</body>
</html>
```